Harrow Grading LLC business card design

Excavation company business cards

Contact Information for Business Card

Harrow Grading LLC cell phone 208-417-6290 office phone 208-319-4856 harrowgradingllc@maplecove.com Driveways, site prep, retaining walls, septic systems, rock delivery

Colors

Designer to choose colors to be used in the design.

```html
<!DOCTYPE html>
<html lang="en">
<head>
<meta charset="utf-8">
<title>Harrow Grading LLC – Business Card</title>
<link rel="stylesheet" href="https://fonts.googleapis.com/css2?family=Roboto:wght@400;500;700&display=swap">
<style>
  :root {
    --bg: #c4c4c4;
    --card: #1d1d1d;
    --card-deep: #161616;
    --orange: #f26a1b;
    --white: #f4f4f4;
    --pattern-light: #3a3a3a;
    --pattern-dark: #1e1e1e;
  }
  * { margin: 0; padding: 0; box-sizing: border-box; }
  html, body { width: 1200px; height: 788px; overflow: hidden; }
  body {
    background: var(--bg);
    font-family: "Roboto", sans-serif;
    position: relative;
  }
  .card {
    position: absolute;
    top: 240px;
    width: 540px;
    height: 309px;
    background: var(--card);
    border-bottom: 3px solid var(--orange);
    box-shadow: 0 10px 24px rgba(0,0,0,0.35);
    overflow: hidden;
  }
  .card--front { left: 40px; }
  .card--back { left: 620px; }

  /* Front */
  .brand {
    position: absolute;
    left: 0; top: 0;
    width: 270px; height: 100%;
    display: flex; align-items: center; justify-content: center;
    gap: 10px;
  }
  .brand__mark {
    width: 14px; height: 14px;
    background: var(--orange);
  }
  .brand__name {
    color: var(--orange);
    font-weight: 700;
    font-size: 22px;
    letter-spacing: 0.5px;
  }
  .divider {
    position: absolute;
    left: 270px; top: 70px;
    width: 1px; height: 170px;
    background: var(--orange);
  }
  .contact {
    position: absolute;
    left: 296px; top: 72px;
    color: var(--white);
  }
  .contact__name {
    color: var(--orange);
    font-weight: 700;
    font-size: 20px;
    text-transform: uppercase;
    letter-spacing: 0.3px;
  }
  .contact__title {
    font-size: 15px;
    margin: 2px 0 16px;
  }
  .contact__list { list-style: none; }
  .contact__item {
    display: flex; align-items: center; gap: 7px;
    font-size: 12.5px;
    line-height: 21px;
  }
  .contact__icon { width: 11px; height: 11px; flex: none; fill: var(--orange); }

  /* Back */
  .pattern {
    position: absolute; inset: 0 0 0 0;
    background: linear-gradient(160deg, var(--pattern-light) 0%, var(--card) 55%, var(--pattern-dark) 100%);
  }
  .services {
    position: absolute;
    left: 60px; bottom: 42px;
    display: grid;
    grid-template-columns: auto auto auto;
    column-gap: 34px;
    row-gap: 4px;
    list-style: none;
    color: var(--white);
    font-size: 16px;
    font-weight: 500;
  }
  .services__item::before {
    content: "";
    display: inline-block;
    width: 5px; height: 5px;
    border-radius: 50%;
    background: var(--orange);
    margin-right: 7px;
    vertical-align: middle;
  }
</style>
</head>
<body>

<section class="card card--front">
  <div class="brand">
    <span class="brand__mark"></span>
    <span class="brand__name">Harrow Grading LLC</span>
  </div>
  <div class="divider"></div>
  <div class="contact">
    <h1 class="contact__name">Dale Mercer</h1>
    <p class="contact__title">Founder</p>
    <ul class="contact__list">
      <li class="contact__item">
        <svg class="contact__icon" viewBox="0 0 24 24"><path d="M6.6 10.8a15.2 15.2 0 0 0 6.6 6.6l2.2-2.2a1 1 0 0 1 1-.25 11.4 11.4 0 0 0 3.6.57 1 1 0 0 1 1 1V20a1 1 0 0 1-1 1A17 17 0 0 1 3 4a1 1 0 0 1 1-1h3.5a1 1 0 0 1 1 1c0 1.25.2 2.45.57 3.57a1 1 0 0 1-.25 1z"/></svg>
        208-319-4856
      </li>
      <li class="contact__item">
        <svg class="contact__icon" viewBox="0 0 24 24"><path d="M7 1h10a2 2 0 0 1 2 2v18a2 2 0 0 1-2 2H7a2 2 0 0 1-2-2V3a2 2 0 0 1 2-2zm0 3v14h10V4z"/></svg>
        208-417-6290
      </li>
      <li class="contact__item">
        <svg class="contact__icon" viewBox="0 0 24 24"><path d="M2 5h20v14H2zm2 2v.5l8 5 8-5V7z"/></svg>
        harrowgradingllc@maplecove.com
      </li>
      <li class="contact__item">
        <svg class="contact__icon" viewBox="0 0 24 24"><circle cx="12" cy="12" r="10"/></svg>
        www.harrowgradingllc.com
      </li>
    </ul>
  </div>
</section>

<section class="card card--back">
  <div class="pattern" role="img" aria-label="Repeating pattern of excavators over mountain peaks in grey tones, with one orange excavator at the centre"></div>
  <ul class="services">
    <li class="services__item">Driveways</li>
    <li class="services__item">Retaining Walls</li>
    <li class="services__item">Rock Delivery</li>
    <li class="services__item">Site Prep</li>
    <li class="services__item">Septic Systems</li>
  </ul>
</section>

</body>
</html>
```